Marlowe Crest Realty business card design

Looking for an upscale and clean business card design and updated logo. I sell to a very high-end south Florida real estate market.
Target Market(s)
High-end real estate in south Florida real estate market
Industry/Entity Type
Real Estate Agent
Contact Information for Business Card
Marlowe Crest Realty, Inc
738 West Pinecrest Ave, Suite 410/510, Fort Lauderdale, FL 33308
Gary Whitlock - Broker/Owner
954-327-8846 Direct
garyshomes@quellmail.com
Website: DwellTarrowBay.com
Font styles to use
Other font styles liked:
- Copperplate Gothic, Georgia, etc.
Requirements
Must have
- My photo, company name, my name and title, all info stated in Details above
Nice to have
- Luxury home design element, waterfront

```html
<!DOCTYPE html>
<html lang="en">
<head>
<meta charset="utf-8">
<title>Marlowe Crest Realty – Business Card</title>
<link rel="stylesheet" href="https://fonts.googleapis.com/css2?family=EB+Garamond:wght@400&family=Oswald:wght@500&family=Open+Sans:wght@400&display=swap">
<style>
  :root {
    --backdrop: #2b2e33;
    --card: #ffffff;
    --ink: #1a1a1a;
    --muted: #555555;
    --rule: #6e6e6e;
    --sun: #f4c531;
    --band-dark: #000000;
  }
  * { box-sizing: border-box; margin: 0; padding: 0; }
  html, body { width: 1200px; height: 900px; overflow: hidden; }
  body { background: var(--backdrop); position: relative; font-family: "Open Sans", Arial, sans-serif; }

  .card {
    position: absolute;
    width: 560px;
    height: 320px;
    background: var(--card);
    border-radius: 22px;
    overflow: hidden;
    box-shadow: 0 18px 40px rgba(0,0,0,.45);
  }
  .card--back { left: 580px; top: 70px; }
  .card--front { left: 60px; top: 480px; }

  .brand { display: flex; align-items: center; gap: 14px; }
  .brand__dot { border-radius: 50%; background: var(--sun); flex: none; }
  .brand__name { font-family: "EB Garamond", Georgia, serif; font-weight: 400; color: var(--ink); white-space: nowrap; }

  .card--back .brand { position: absolute; left: 50%; top: 50%; transform: translate(-50%, -50%); }
  .card--back .brand__dot { width: 110px; height: 110px; }
  .card--back .brand__name { font-size: 30px; }

  .card--front .brand { position: absolute; left: 190px; top: 34px; }
  .card--front .brand__dot { width: 92px; height: 92px; }
  .card--front .brand__name { font-size: 24px; }

  .agent { position: absolute; left: 40px; top: 140px; }
  .agent__name { font-family: "Oswald", "Arial Narrow", sans-serif; font-weight: 500; font-size: 25px; color: var(--sun); line-height: 1; text-transform: uppercase; }
  .agent__title { font-size: 8px; color: var(--muted); margin-top: 3px; }

  .divider { position: absolute; left: 36px; top: 186px; width: 470px; height: 1px; background: var(--rule); }

  .contacts { position: absolute; left: 40px; top: 198px; list-style: none; }
  .contacts__item { display: flex; align-items: center; gap: 9px; font-size: 13px; color: var(--ink); height: 26px; }
  .contacts__icon { width: 18px; height: 18px; flex: none; }

  .address { position: absolute; right: 44px; top: 204px; text-align: left; font-size: 12px; line-height: 1.45; color: var(--ink); }

  .edge-band { position: absolute; left: 0; bottom: 0; width: 560px; height: 34px; }
</style>
</head>
<body>

  <section class="card card--back" aria-label="Card back">
    <div class="brand">
      <span class="brand__dot"></span>
      <span class="brand__name">Marlowe Crest Realty, Inc</span>
    </div>
  </section>

  <section class="card card--front" aria-label="Card front">
    <div class="brand">
      <span class="brand__dot"></span>
      <span class="brand__name">Marlowe Crest Realty, Inc</span>
    </div>

    <div class="agent">
      <p class="agent__name">Gary Whitlock</p>
      <p class="agent__title">CEO/Managing Director</p>
    </div>

    <div class="divider"></div>

    <ul class="contacts">
      <li class="contacts__item">
        <svg class="contacts__icon" viewBox="0 0 18 18" aria-hidden="true">
          <rect width="18" height="18" rx="4" fill="var(--sun)"/>
          <path d="M6 4.5c.6 0 1.2 1.6 1.2 2.1 0 .5-.8.8-.8 1.3.3 1.1 1.2 2 2.3 2.4.5 0 .8-.8 1.3-.8s2.1.6 2.1 1.2c0 .8-.9 1.8-1.8 1.8C7.5 12.5 4.6 9.6 4.4 6.3c0-.9 1-1.8 1.6-1.8z" fill="#fff"/>
        </svg>
        <span>954-327-8846</span>
      </li>
      <li class="contacts__item">
        <svg class="contacts__icon" viewBox="0 0 18 18" aria-hidden="true">
          <rect width="18" height="18" rx="4" fill="var(--sun)"/>
          <rect x="3.5" y="5.5" width="11" height="7.5" fill="none" stroke="#fff" stroke-width="1.2"/>
          <path d="M3.5 5.5 9 10l5.5-4.5" fill="none" stroke="#fff" stroke-width="1.2"/>
        </svg>
        <span>garyshomes@quellmail.com</span>
      </li>
      <li class="contacts__item">
        <svg class="contacts__icon" viewBox="0 0 18 18" aria-hidden="true">
          <rect width="18" height="18" rx="4" fill="var(--sun)"/>
          <circle cx="9" cy="9" r="5" fill="none" stroke="#fff" stroke-width="1.1"/>
          <ellipse cx="9" cy="9" rx="2.2" ry="5" fill="none" stroke="#fff" stroke-width="1"/>
          <path d="M4 9h10" stroke="#fff" stroke-width="1"/>
        </svg>
        <span>www.DwellTarrowBay.com</span>
      </li>
    </ul>

    <p class="address">738 West Pinecrest Ave<br>Suite 410/510, Fort Lauderdale, FL 33308</p>

    <svg class="edge-band" viewBox="0 0 560 34" preserveAspectRatio="none" aria-hidden="true">
      <rect x="0" y="22" width="250" height="12" fill="var(--sun)"/>
      <polygon points="250,0 560,22 560,34 250,34" fill="var(--band-dark)"/>
    </svg>
  </section>

</body>
</html>
```